menu board design: rustle burger

we are a burger restaurant.
we need to re design our menu board to fit within the new design of the restaurant. we are after something simple and easy to read. the overall look and feel of the design should be inline with the design of the shop.

Target Market(s)

18-40 male and female

Colors

Designer to choose colors to be used in the design.

Requirements
Must have
• easy to read. good layout. white background. branding included in design.

```html
<!DOCTYPE html>
<html lang="en">
<head>
<meta charset="utf-8">
<title>Rustle Burger Menu Board</title>
<link rel="stylesheet" href="https://fonts.googleapis.com/css2?family=Bebas+Neue&family=Montserrat:wght@500;600;700;800&display=swap">
<style>
  :root {
    --brand-blue: #1f56a6;
    --ink: #1a1a1a;
    --board: #f1f1f1;
    --paper: #ffffff;
    --faint-blue: #d3dcea;
    --divider: #bdbdbd;
  }
  * { box-sizing: border-box; margin: 0; padding: 0; }
  html, body { width: 1200px; height: 500px; overflow: hidden; background: var(--paper); }
  .menu-board {
    position: relative; width: 1200px; height: 500px;
    font-family: "Montserrat", sans-serif; color: var(--ink);
  }
  .frame-outer {
    position: absolute; left: 11px; top: 11px; width: 1178px; height: 478px;
    border: 4px solid var(--brand-blue); border-radius: 12px; background: var(--board);
  }
  .frame-inner {
    position: absolute; left: 17px; top: 17px; width: 1166px; height: 466px;
    border: 1px solid var(--brand-blue); border-radius: 8px;
  }
  .divider {
    position: absolute; top: 124px; height: 248px; border-left: 1px dashed var(--divider);
  }
  .section-title {
    position: absolute; top: 34px; font-family: "Bebas Neue", sans-serif; font-weight: 400;
    font-size: 45px; line-height: 45px; color: var(--brand-blue); letter-spacing: -0.8px;
    white-space: nowrap;
  }
  .section-intro {
    position: absolute; top: 79px; font-size: 8.7px; line-height: 12px; font-weight: 500;
  }
  .nowrap { white-space: nowrap; }
  .menu-item { position: absolute; }
  .item-line {
    display: flex; align-items: baseline; color: var(--brand-blue);
    font-size: 14px; font-weight: 600; line-height: 17px; white-space: nowrap;
    letter-spacing: -0.1px;
  }
  .item-line .leader {
    flex: 1; border-bottom: 2px dotted var(--brand-blue); margin: 0 1px 3px; min-width: 4px;
  }
  .item-desc { font-size: 6px; line-height: 7px; font-weight: 500; margin: 3px 0 0 3px; white-space: nowrap; }
  .caps .item-line { text-transform: uppercase; }
  .caps .item-desc { text-transform: uppercase; }
  .pieces { color: var(--brand-blue); }
  .sides-icon {
    position: absolute; left: 684px; top: 28px; width: 50px; height: 46px;
    background: var(--brand-blue); border-radius: 3px;
  }
  .sauce-note {
    position: absolute; left: 622px; top: 410px; font-size: 8.5px; font-weight: 800;
    line-height: 12px; color: var(--ink);
  }
  .sauce-note .bbq { font-size: 19px; letter-spacing: 0.5px; }
  .pack-list { position: absolute; left: 736px; top: 408px; width: 125px; }
  .pack-row {
    display: flex; align-items: baseline; font-size: 10px; font-weight: 500; line-height: 15.5px;
  }
  .pack-row .leader { flex: 1; border-bottom: 1px dotted var(--ink); margin: 0 1px 3px; }
  .brand-name {
    position: absolute; left: 222px; top: 400px; display: flex; align-items: center; gap: 8px;
    font-size: 28px; font-weight: 800; color: var(--brand-blue);
  }
  .brand-dot { width: 14px; height: 14px; border-radius: 50%; background: var(--brand-blue); }
  .brand-name-faint {
    position: absolute; left: 1010px; top: 418px; font-size: 22px; font-weight: 800; color: var(--faint-blue);
  }
</style>
</head>
<body>
<main class="menu-board">
  <div class="frame-outer"></div>
  <div class="frame-inner"></div>

  <div class="divider" style="left:303px"></div>
  <div class="divider" style="left:596px"></div>
  <div class="divider" style="left:887px"></div>

  <!-- Beef burgers -->
  <h2 class="section-title" style="left:32px">Beef Burgers</h2>
  <p class="section-intro" style="left:34px;width:268px">100% natural beef without any additives or perservatives. We know because we grind it ourselves! Smashed to order on a hot grill rite in front of you.</p>
  <section class="beef-list">
    <div class="menu-item" style="left:37px;top:131px;width:235px"><div class="item-line">CHEESEBURGER<span class="leader"></span>9.5</div><p class="item-desc">Dill Pickles, minced onion, American cheddar,<br>mustard and ketchup.</p></div>
    <div class="menu-item" style="left:37px;top:169px;width:234px"><div class="item-line">Flame Grill<span class="leader"></span>9.5</div><p class="item-desc">Shredded lettuce, sliced tomato, minced onion,<br>dill pickles,american chedar, mayo and ketchup.</p></div>
    <div class="menu-item" style="left:37px;top:207px;width:235px"><div class="item-line">Big Mic<span class="leader"></span>9.9</div><p class="item-desc">Shredded lettuce, dill pickles, minced onion,<br>American cheddar and special sauce.</p></div>
    <div class="menu-item" style="left:37px;top:245px;width:235px"><div class="item-line">Truffled<span class="leader"></span>9.9</div><p class="item-desc">Fresh Rocket, caramelised onion, dill pickles,<br>havarti cheese and truffle infused mayo</p></div>
    <div class="menu-item" style="left:37px;top:283px;width:234px"><div class="item-line">CHEESE DELUXE<span class="leader"></span>9.5</div><p class="item-desc">Caramelised onion, american chedar,<br>dill pickles and special sauce.</p></div>
    <div class="menu-item" style="left:37px;top:321px;width:234px"><div class="item-line">CALI BURGER<span class="leader"></span>9.9</div><p class="item-desc">Iceburg lettuce, sliced tomato, American chedar,<br>minced onion, crinkle cut pickleS, pink sauce.</p></div>
  </section>

  <!-- Chicken burgers -->
  <h2 class="section-title" style="left:336px">Chicken Burgers</h2>
  <p class="section-intro nowrap" style="left:337px">Famous southern style fried chicken with secret seasoning</p>
  <section class="chicken-list">
    <div class="menu-item" style="left:335px;top:131px;width:238px"><div class="item-line">ORIGINAL<span class="leader"></span>8.9</div><p class="item-desc">Shredded lettuce and mayo.</p></div>
    <div class="menu-item" style="left:335px;top:169px;width:237px"><div class="item-line">HOT N SPICY<span class="leader"></span>9.5</div><p class="item-desc">Shredded lettuce, mayo and pirri pirri.</p></div>
    <div class="menu-item" style="left:335px;top:207px;width:237px"><div class="item-line">KENTUCKY<span class="leader"></span>9.9</div><p class="item-desc">Shredded lettuce, swiss cheese and feisty mayo.</p></div>
    <div class="menu-item" style="left:335px;top:245px;width:238px"><div class="item-line">BUFFALO BILL<span class="leader"></span>9.9</div><p class="item-desc">smothered in hot sauce, creamy slaw, american chedar and ranch.</p></div>
    <div class="menu-item" style="left:335px;top:283px;width:240px"><div class="item-line" style="letter-spacing:-0.4px">SOUTHERN FRIED CHICKEN<span class="leader"></span>9.9</div><p class="item-desc">Creamy slaw, crinkle cut pickles, american chedar and chipotle mayo.</p></div>
    <div class="menu-item" style="left:335px;top:321px;width:238px"><div class="item-line">SMOKY BBQ<span class="leader"></span>9.9</div><p class="item-desc">smothered in smoky bbq, creamy slaw, american chedar and ranch.</p></div>
  </section>

  <!-- Sides -->
  <div class="sides-icon" role="img" aria-label="Icon of fries and a burger with a drink cup"></div>
  <h2 class="section-title" style="left:754px">Sides</h2>
  <section class="sides-list caps">
    <div class="menu-item" style="left:621px;top:130px;width:241px"><div class="item-line" style="text-transform:none">Fries<span class="leader"></span>3.5</div></div>
    <div class="menu-item" style="left:621px;top:153px;width:242px"><div class="item-line" style="text-transform:none">Kentucky Tenders<span class="leader"></span>6.9</div><p class="item-desc" style="text-transform:none">Breaded and fried chicken with secret seasoning <span class="pieces">(2 pcs)</span></p></div>
    <div class="menu-item" style="left:622px;top:191px;width:238px"><div class="item-line">Onion Rings<span class="leader"></span>5.0</div><p class="item-desc">Battered and fried onion rings</p></div>
    <div class="menu-item" style="left:622px;top:229px;width:240px"><div class="item-line">Guacamole Nachos<span class="leader"></span>11.5</div><p class="item-desc">Freshly cooked corn chips, salsa, jalapeno,<br>sour cream, cheese sauce and guacamole.</p></div>
    <div class="menu-item" style="left:621px;top:267px;width:242px"><div class="item-line">Beef Chilli Nachos<span class="leader"></span>11.5</div><p class="item-desc">Freshly cooked corn chips, salsa, jalapeno,<br>sour cream, cheese sauce and beef chilli</p></div>
    <div class="menu-item" style="left:621px;top:305px;width:238px"><div class="item-line">Machos Nachos<span class="leader"></span>13.5</div><p class="item-desc">Beef and guacamole nachos.</p></div>
    <div class="menu-item" style="left:622px;top:340px;width:240px"><div class="item-line">Coleslaw<span class="leader"></span>5.0</div><p class="item-desc">Classic creamy slaw</p></div>
    <div class="menu-item" style="left:622px;top:374px;width:240px"><div class="item-line">Bufallo Ribs</div><p class="item-desc">Bufallo style chicken ribs smothered in either</p></div>
  </section>
  <p class="sauce-note">CLASSIC HOT SAUCE<br>OR SMOKY <span class="bbq">BBQ</span></p>
  <div class="pack-list">
    <div class="pack-row">6 PACK<span class="leader"></span>6.9</div>
    <div class="pack-row">12 PACK<span class="leader"></span>12.9</div>
    <div class="pack-row">24 PACK<span class="leader"></span>23.9</div>
  </div>

  <!-- Ribs loaded fries -->
  <h2 class="section-title" style="left:913px">Ribs Loaded Fries</h2>
  <p class="section-intro nowrap" style="left:914px">A selection of classic loaded fried combinations</p>
  <section class="fries-list caps">
    <div class="menu-item" style="left:915px;top:131px;width:237px"><div class="item-line">Cheesy Fries<span class="leader"></span>5.5</div><p class="item-desc">With chedar cheese sauce</p></div>
    <div class="menu-item" style="left:915px;top:169px;width:237px"><div class="item-line" style="letter-spacing:-0.4px">Creamy Mushroom Fries<span class="leader"></span>6.9</div><p class="item-desc">With classic creamy mushroom sauce</p></div>
    <div class="menu-item" style="left:915px;top:207px;width:237px"><div class="item-line">Classic Gravy Fries<span class="leader"></span>5.5</div><p class="item-desc">With chedar cheese sauce</p></div>
    <div class="menu-item" style="left:914px;top:245px;width:238px"><div class="item-line">Parmesan&nbsp; Truffle<span class="leader"></span>6.9</div><p class="item-desc">With truffle infused mayo and parmesan cheese</p></div>
    <div class="menu-item" style="left:914px;top:283px;width:238px"><div class="item-line">Beef Chilli Fries<span class="leader"></span>9.9</div><p class="item-desc">With salsa, jalapeno, sour cream, cheese sauce and beef chilli</p></div>
    <div class="menu-item" style="left:914px;top:321px;width:238px"><div class="item-line">Guacamole Fries<span class="leader"></span>9.9</div><p class="item-desc">With salsa, jalapeno, sour cream, cheese sauce and guacamole.</p></div>
    <div class="menu-item" style="left:914px;top:359px;width:238px"><div class="item-line">Machos Fries<span class="leader"></span>11.5</div><p class="item-desc">With beef and guacamole.</p></div>
  </section>

  <!-- Branding -->
  <div class="brand-name"><span class="brand-dot"></span>Rustle Burger</div>
  <div class="brand-name-faint">Rustle Burger</div>
</main>
</body>
</html>
```